Quillbay.vc needs a better website design!

We need a new and better website for Quillbay.vc. We're a Canadian venture capital firm that invests in innovative entrepreneurs. We compete against the following websites: tormelo.vc, brightvalefund.ca, kestrowvc.com, and dovaran.vc. We're a diverse group of partners and we're dedicated to the founders we invest in.
Updates

I don’t really like stock photos of random people as part of the website design…so please try to stay away from using those images. Thanks, Owen

Target Market(s)

Canadian entrepreneurs and investors

Industry/Entity Type

Venture capital, finance, investment, entrepreneurship

Coding

Coded - Design and coding required

Number of Pages Required

4 page

Font styles to use
Sans Serif

Colors

Designer to choose colors to be used in the design.

Requirements
Must have
• Clean crisp overall design. Fast and to the point.
Nice to have
• Check out www.quillbay.vc - I did it myself and it is too basic and too wordy.
Should not have
• No stock images with random people in them! Not too wordy or with too many large images that are slow to load.

```html
<!DOCTYPE html>
<html lang="en">
<head>
<meta charset="utf-8">
<title>Quillbay.vc — Venture Capital</title>
<link href="https://fonts.googleapis.com/css2?family=Poppins:wght@400;500;600&display=swap" rel="stylesheet">
<style>
:root{
  --green:#7a9a2e;
  --green-band:#7b9a32;
  --ink:#1f2a0b;
  --text:#2d2d2d;
  --muted:#555;
  --line:#e2e2e2;
  --footer:#f5f5f5;
  --bar:#2b2e22;
  --white:#fff;
}
*{margin:0;padding:0;box-sizing:border-box}
html,body{width:1200px;height:2276px;overflow:hidden}
body{font-family:'Poppins',sans-serif;color:var(--text);background:var(--white);position:relative}
.abs{position:absolute}

/* header */
.site-header{position:absolute;left:0;top:0;width:1200px;height:97px;background:var(--white);border-bottom:1px solid var(--line)}
.brand{position:absolute;left:162px;top:30px;display:flex;align-items:center;gap:10px;font-weight:600;font-size:22px;color:var(--green)}
.brand-dot{width:22px;height:22px;border-radius:50%;background:var(--green)}
.nav a{position:absolute;top:0;height:100px;line-height:100px;font-size:13.5px;color:#444;text-decoration:none}
.nav .active{left:586px;width:64px;text-align:center;background:#f2f2f2;color:var(--green);border-bottom:3px solid var(--green)}

/* hero */
.hero{position:absolute;left:0;top:97px;width:1200px;height:575px}
.hero-photo{position:absolute;inset:0;background:linear-gradient(180deg,#6e7468 0%,#46583a 35%,#2f4a26 70%,#3c5a28 100%)}
.hero-title{position:absolute;left:150px;top:135px;width:900px;text-align:center;color:var(--white);font-weight:500;font-size:28px;line-height:47px}
.numbers-label{position:absolute;left:262px;top:330px;width:676px;display:flex;align-items:center;gap:24px;color:var(--white);font-size:19px}
.numbers-label::before,.numbers-label::after{content:"";flex:1;height:1px;background:rgba(255,255,255,.35)}
.stat{position:absolute;top:375px;width:164px;height:59px;border:1px solid rgba(255,255,255,.4);display:flex;align-items:center;justify-content:center;gap:8px;color:var(--white)}
.stat b{font-weight:500;font-size:36px;line-height:1}
.stat span{font-size:13.5px;line-height:15px}
.hero-wave{position:absolute;left:0;bottom:0;width:1200px;height:90px}

/* provide */
.section-title{position:absolute;left:0;width:1200px;text-align:center;color:var(--ink);font-weight:500;font-size:27px;line-height:42px}
.dots{position:absolute;background:#f4f4f4}
.card{position:absolute;top:829px;width:419px;height:269px;border:1px solid #ddd;border-radius:6px;background:var(--white);box-shadow:0 2px 6px rgba(0,0,0,.05)}
.card svg{position:absolute;left:33px;top:48px}
.card p{position:absolute;left:33px;top:138px;width:370px;font-size:19.5px;line-height:32px;color:var(--text)}

/* portfolio */
.tile{position:absolute;width:154px;height:67px;border:1px solid #eee;border-radius:3px;box-shadow:0 2px 5px rgba(0,0,0,.06);display:flex;align-items:center;justify-content:center;font-size:17px;font-weight:500;color:#333}

/* call to action */
.cta{position:absolute;left:0;top:1511px;width:1200px;height:451px;background:linear-gradient(135deg,#7fa036 0%,#738f2c 45%,#809f38 100%)}
.cta h2{position:absolute;left:208px;top:135px;color:var(--white);font-weight:500;font-size:51px;line-height:63px}
.cta p{position:absolute;left:208px;top:270px;color:var(--white);font-size:27px}

/* footer */
.site-footer{position:absolute;left:0;top:1962px;width:1200px;height:269px;background:var(--footer)}
.footer-brand{position:absolute;left:162px;top:105px;display:flex;align-items:center;gap:12px;font-weight:600;font-size:30px;color:var(--green)}
.footer-brand i{width:30px;height:30px;border-radius:50%;background:var(--green)}
.footer-col h3{position:absolute;font-weight:500;font-size:19.5px;color:var(--ink)}
.links a{position:absolute;left:530px;font-size:13.5px;color:#333;text-decoration:none}
.links a::before{content:"›";margin-right:10px;color:#555}
.email{position:absolute;left:852px;top:96px;font-size:13.5px;color:#333;display:flex;align-items:center;gap:10px}
.social{position:absolute;top:179px;width:30px;height:30px;border-radius:50%}
.copyright{position:absolute;left:0;top:2231px;width:1200px;height:45px;background:var(--bar);color:var(--white);font-size:13.5px;text-align:center;line-height:45px}
</style>
</head>
<body>

<header class="site-header">
  <div class="brand"><span class="brand-dot"></span>Quillbay.vc</div>
  <nav class="nav">
    <a class="active" href="#">Home</a>
    <a href="#" style="left:691px">Team</a>
    <a href="#" style="left:785px">Companies</a>
    <a href="#" style="left:919px">What We Look For</a>
  </nav>
</header>

<section class="hero">
  <div class="hero-photo" role="img" aria-label="Misty green mountain valley landscape"></div>
  <h1 class="hero-title">Quillbay.vc is a venture capital firm that invests in innovative seed-stage technology companies in Western Canada focused on B2B and SaaS markets.</h1>
  <div class="numbers-label">Quillbay.vc in numbers</div>
  <div class="stat" style="left:334px"><b>10</b><span>Portfolio<br>companies</span></div>
  <div class="stat" style="left:518px"><b>7</b><span>Follow-on<br>financings</span></div>
  <div class="stat" style="left:702px"><b>100</b><span>+<br>Employees</span></div>
  <svg class="hero-wave" viewBox="0 0 1200 90" preserveAspectRatio="none">
    <path d="M0 45 C120 -5 260 0 420 25 C600 55 760 100 960 80 C1060 70 1140 50 1200 40 L1200 90 L0 90 Z" fill="#fff"/>
  </svg>
</section>

<h2 class="section-title" style="top:707px">We are serial entrepreneurs and venture<br>capital investors who provide</h2>

<div class="dots" style="left:968px;top:800px;width:100px;height:100px" role="img" aria-label="Light dotted decoration"></div>
<div class="dots" style="left:132px;top:1020px;width:100px;height:100px" role="img" aria-label="Light dotted decoration"></div>

<div class="card" style="left:162px">
  <svg width="82" height="78" viewBox="0 0 82 78" fill="none" stroke-width="2.5">
    <rect x="2" y="56" width="13" height="20" stroke="#999"/>
    <rect x="22" y="44" width="13" height="32" stroke="#999"/>
    <rect x="42" y="30" width="13" height="46" stroke="#999"/>
    <rect x="62" y="14" width="13" height="62" stroke="#999"/>
    <path d="M4 32 C28 30 44 20 56 4" stroke="#7a9a2e"/>
    <path d="M48 4 L57 2 L57 11" stroke="#7a9a2e"/>
  </svg>
  <p>Mentoring and strategic advice to help you grow your company quickly and efficiently</p>
</div>
<div class="card" style="left:619px">
  <svg width="82" height="78" viewBox="0 0 82 78" fill="none" stroke-width="2.5">
    <circle cx="50" cy="50" r="24" stroke="#7a9a2e"/>
    <text x="50" y="61" text-anchor="middle" font-family="Poppins,sans-serif" font-size="30" fill="#7a9a2e">$</text>
  </svg>
  <p>Investor introductions to help you raise additional follow-on funding for your startup</p>
</div>

<h2 class="section-title" style="top:1183px;font-size:25px">Check out our innovative portfolio companies!</h2>

<div class="tile" style="left:162px;top:1259px">Ravelin Loop</div>
<div class="tile" style="left:343px;top:1259px">Cordwise</div>
<div class="tile" style="left:523px;top:1259px">pacerun</div>
<div class="tile" style="left:704px;top:1259px">TALLYOPS</div>
<div class="tile" style="left:885px;top:1259px">brindle</div>
<div class="tile" style="left:162px;top:1348px">Fundaro</div>
<div class="tile" style="left:343px;top:1348px">Gamelyst</div>
<div class="tile" style="left:523px;top:1348px">Easeway</div>
<div class="tile" style="left:704px;top:1348px">Keypath</div>
<div class="tile" style="left:885px;top:1348px">nutrifold</div>

<section class="cta">
  <h2>If you have what<br>we're looking for</h2>
  <p>Contact us today</p>
</section>

<footer class="site-footer">
  <div class="footer-brand"><i></i>Quillbay.vc</div>
  <div class="footer-col">
    <h3 style="left:530px;top:52px">Quick Links</h3>
    <h3 style="left:852px;top:54px">Get In Touch</h3>
    <h3 style="left:852px;top:139px">Follow Us</h3>
  </div>
  <div class="links">
    <a href="#" style="top:95px">Home</a>
    <a href="#" style="top:128px">What</a>
    <a href="#" style="top:160px">Who</a>
    <a href="#" style="top:192px">Portfolio</a>
  </div>
  <div class="email">
    <svg width="14" height="11" viewBox="0 0 14 11"><rect width="14" height="11" rx="1" fill="#7a9a2e"/><path d="M1 1 L7 6 L13 1" stroke="#fff" fill="none" stroke-width="1.3"/></svg>
    info@quillbay.vc
  </div>
  <span class="social" style="left:854px;background:#1da1f2"></span>
  <span class="social" style="left:891px;background:#0a78b5"></span>
</footer>

<div class="copyright">Copyright © 2021 Quillbay.vc - All Rights Reserved.</div>

</body>
</html>
```